German Headhunter/ HR Consultancy needs Business Cards Design

We need a business Card Design for our Company in Stuttgart. We are specialized as Headhunter/ HR Consultancy in Placement of specialist and managers in permanent employment. Please refer to our business logo.

```html
<!DOCTYPE html>
<html lang="en">
<head>
<meta charset="utf-8">
<title>Kernwerk Personalberatung – Business Card</title>
<link rel="stylesheet" href="https://fonts.googleapis.com/css2?family=Arimo:wght@400;700&display=swap">
<style>
  :root {
    --brand-blue: #3450a8;
    --brand-blue-dark: #2b4595;
    --brand-grey: #8e8f93;
    --ink: #1d1d1f;
    --paper: #ffffff;
    --backdrop: #2a2b2e;
    --divider: #9a9a9a;
  }
  * { margin: 0; padding: 0; box-sizing: border-box; }
  html, body { width: 1200px; height: 900px; overflow: hidden; }
  body {
    background: var(--backdrop);
    font-family: "Arimo", Arial, sans-serif;
    position: relative;
  }
  .card {
    position: absolute;
    left: 300px;
    width: 600px;
    height: 340px;
    border-radius: 18px;
    overflow: hidden;
  }
  .card--front { top: 90px; background: var(--paper); }
  .card--back { top: 470px; background: var(--brand-blue); }

  .front-swoosh { position: absolute; inset: 0; width: 100%; height: 100%; }

  .brand {
    position: absolute;
    display: flex;
    align-items: center;
    gap: 12px;
  }
  .brand-mark {
    width: 26px; height: 26px;
  }
  .brand-text { line-height: 1; font-weight: 700; }
  .brand-name { font-size: 30px; letter-spacing: 1px; }
  .brand-sub { font-size: 12px; letter-spacing: 2.6px; margin-top: 5px; font-weight: 400; }

  .card--front .brand { left: 40px; top: 86px; }
  .card--front .brand-mark { background: var(--brand-blue); }
  .card--front .brand-name { color: var(--brand-blue); }
  .card--front .brand-sub { color: var(--brand-grey); }

  .divider {
    position: absolute;
    left: 318px; top: 62px;
    width: 1px; height: 150px;
    background: var(--divider);
  }

  .contact {
    position: absolute;
    left: 340px; top: 58px;
    color: var(--ink);
  }
  .contact-name {
    font-size: 22px; font-weight: 700; color: var(--brand-blue);
    letter-spacing: 0.5px;
  }
  .contact-role { font-size: 13px; margin-top: 2px; }
  .contact-list { list-style: none; margin-top: 12px; font-size: 12.5px; }
  .contact-list li { display: flex; align-items: center; gap: 7px; margin-bottom: 5px; }
  .contact-list svg { width: 12px; height: 12px; flex: none; }
  .address { font-size: 12.5px; line-height: 1.4; margin-top: 2px; }

  .back-pattern {
    position: absolute; inset: 0;
    background: linear-gradient(135deg, var(--brand-blue) 0%, var(--brand-blue-dark) 100%);
  }
  .card--back .brand { left: 44px; bottom: 52px; }
  .card--back .brand-mark { background: var(--paper); }
  .card--back .brand-name,
  .card--back .brand-sub { color: var(--paper); }
</style>
</head>
<body>

<section class="card card--front" aria-label="Business card front">
  <svg class="front-swoosh" viewBox="0 0 600 340" preserveAspectRatio="none" aria-hidden="true">
    <path d="M0,205 C140,265 380,318 600,330 L600,340 L0,340 Z" fill="var(--brand-blue)"/>
    <path d="M150,262 C300,305 460,322 600,322" fill="none" stroke="var(--brand-grey)" stroke-width="4"/>
    <path d="M150,262 C300,305 460,322 600,322 L600,330 C380,318 260,292 150,262 Z" fill="var(--paper)"/>
  </svg>

  <div class="brand">
    <span class="brand-mark"></span>
    <div class="brand-text">
      <div class="brand-name">KERNWERK</div>
      <div class="brand-sub">PERSONALBERATUNG</div>
    </div>
  </div>

  <span class="divider"></span>

  <div class="contact">
    <h1 class="contact-name">JONAS BERGER</h1>
    <p class="contact-role">CEO/Founder</p>
    <ul class="contact-list">
      <li>
        <svg viewBox="0 0 24 24" aria-hidden="true"><path fill="var(--brand-blue)" d="M6.6 10.8a15 15 0 0 0 6.6 6.6l2.2-2.2a1 1 0 0 1 1-.25 11.4 11.4 0 0 0 3.6.6 1 1 0 0 1 1 1V20a1 1 0 0 1-1 1A17 17 0 0 1 3 4a1 1 0 0 1 1-1h3.5a1 1 0 0 1 1 1c0 1.25.2 2.45.6 3.6a1 1 0 0 1-.25 1z"/></svg>
        (555) 010 - 2843
      </li>
      <li>
        <svg viewBox="0 0 24 24" aria-hidden="true"><rect x="2" y="5" width="20" height="14" rx="1" fill="var(--brand-blue)"/><path d="M2 6l10 7 10-7" fill="none" stroke="#fff" stroke-width="1.8"/></svg>
        info@kernwerkpersonal.com
      </li>
      <li>
        <svg viewBox="0 0 24 24" aria-hidden="true"><circle cx="12" cy="12" r="10" fill="var(--brand-blue)"/><path d="M2 12h20M12 2c3 3 3 17 0 20M12 2c-3 3-3 17 0 20" fill="none" stroke="#fff" stroke-width="1.4"/></svg>
        www.kernwerkpersonal.com
      </li>
    </ul>
    <p class="address">52 Lindenweg Road<br>Ste C Country Name, 7012</p>
  </div>
</section>

<section class="card card--back" aria-label="Business card back">
  <div class="back-pattern" role="img" aria-label="Repeating brand pattern in tones of blue"></div>
  <div class="brand">
    <span class="brand-mark"></span>
    <div class="brand-text">
      <div class="brand-name">KERNWERK</div>
      <div class="brand-sub">PERSONALBERATUNG</div>
    </div>
  </div>
</section>

</body>
</html>
```